Brisk Coatings business card for residential and commercial painting

A clean, professional design. Easy to read
Eye catching and elegant
Front could have some color variations
On the back of card I would like all black with signature logo

*Attached is my current business card and the items I want displayed

Contact Information for Business Card

Email, phone number, website, and owner name

Font styles to use
Serif

Requirements
Must have
• My logo with cool design and perhaps some paint splatter

```html
<!DOCTYPE html>
<html lang="en">
<head>
<meta charset="utf-8">
<title>Brisk Coatings business cards</title>
<link rel="stylesheet" href="https://fonts.googleapis.com/css2?family=Merriweather:wght@400;700&display=swap">
<style>
  :root {
    --backdrop: #6c6768;
    --paper: #f7f7f7;
    --black: #111111;
    --brand-blue: #1172bf;
    --ink: #2b2b2b;
    --rule-light: #b9b9b9;
    --rule-dark: #4a4a4a;
    --muted: #8a8a8a;
    --white: #ffffff;
  }
  html, body {
    margin: 0;
    width: 1200px;
    height: 1200px;
    overflow: hidden;
    background: var(--backdrop);
    font-family: "Merriweather", serif;
  }
  .card {
    position: absolute;
    width: 594px;
    height: 349px;
    border-radius: 20px;
    overflow: hidden;
  }
  .card--back { left: 298px; top: 199px; background: var(--black); }
  .card--front { left: 292px; top: 637px; background: var(--paper); }

  .wordmark {
    position: absolute;
    left: 0;
    right: 0;
    display: flex;
    justify-content: center;
    align-items: center;
    gap: 12px;
    font-weight: 700;
    text-transform: uppercase;
    letter-spacing: 0.5px;
    white-space: nowrap;
  }
  .wordmark__splatter {
    display: inline-block;
    border-radius: 50%;
    background: var(--brand-blue);
  }
  .card--back .wordmark { top: 36px; font-size: 26px; color: var(--white); }
  .card--back .wordmark__splatter { width: 22px; height: 22px; }
  .card--front .wordmark { top: 56px; font-size: 36px; color: var(--ink); }
  .card--front .wordmark__splatter { width: 30px; height: 30px; }

  .price-list { position: absolute; left: 35px; width: 525px; top: 96px; }
  .price-line {
    position: relative;
    height: 42px;
    border-bottom: 2px solid var(--rule-dark);
    box-sizing: border-box;
  }
  .price-line:last-child { border-bottom: none; }
  .price-line__symbol {
    position: absolute;
    left: 17px;
    bottom: 4px;
    font-size: 17px;
    color: var(--muted);
  }

  .band { position: absolute; left: 0; bottom: 0; width: 100%; }
  .band--back { height: 44px; }
  .band--front { top: 120px; height: 229px; }

  .back-url {
    position: absolute;
    left: 0;
    right: 0;
    top: 318px;
    text-align: center;
    color: var(--white);
    font-size: 13px;
    letter-spacing: 6px;
  }

  .owner {
    position: absolute;
    right: 318px;
    top: 216px;
    text-align: right;
    color: var(--white);
    white-space: nowrap;
  }
  .owner__name { font-size: 20px; font-weight: 700; line-height: 30px; }
  .owner__title { font-size: 13px; line-height: 22px; }

  .contact {
    position: absolute;
    left: 306px;
    top: 219px;
    color: var(--white);
    font-size: 13.5px;
    line-height: 25px;
    white-space: nowrap;
  }
  .contact__item { display: flex; align-items: center; gap: 9px; }
  .contact__icon { width: 16px; height: 14px; flex: none; }

  .front-url {
    position: absolute;
    left: 0;
    right: 0;
    top: 292px;
    display: flex;
    justify-content: center;
    align-items: center;
    gap: 22px;
    color: var(--white);
    font-size: 14px;
  }
  .front-url__rule { width: 110px; height: 1px; background: var(--white); }
</style>
</head>
<body>

<section class="card card--back">
  <div class="wordmark"><span>Brisk</span><span class="wordmark__splatter" role="img" aria-label="Blue paint splatter mark"></span><span>Coatings</span></div>
  <div class="price-list">
    <div class="price-line"><span class="price-line__symbol">$</span></div>
    <div class="price-line"><span class="price-line__symbol">$</span></div>
    <div class="price-line"><span class="price-line__symbol">$</span></div>
    <div class="price-line"><span class="price-line__symbol">$</span></div>
    <div class="price-line"><span class="price-line__symbol">$</span></div>
  </div>
  <svg class="band band--back" viewBox="0 0 594 44" preserveAspectRatio="none">
    <path d="M0 4 L60 3 L110 5 L200 2 L250 4 L330 1 L400 4 L470 2 L530 3 L594 1 L594 44 L0 44 Z" fill="var(--brand-blue)"/>
  </svg>
  <div class="back-url">www.briskcoatingstn.com</div>
</section>

<section class="card card--front">
  <div class="wordmark"><span>Brisk</span><span class="wordmark__splatter" role="img" aria-label="Blue paint splatter mark"></span><span>Coatings</span></div>
  <svg class="band band--front" viewBox="0 0 594 229" preserveAspectRatio="none">
    <path d="M0 10 Q297 75 594 18 L594 229 L0 229 Z" fill="var(--brand-blue)"/>
  </svg>
  <div class="owner">
    <div class="owner__name">Marcos "MJ"</div>
    <div class="owner__title">Owner - Licensed &amp; Insured</div>
  </div>
  <div class="contact">
    <div class="contact__item">
      <svg class="contact__icon" viewBox="0 0 16 14"><path d="M1 5 Q8 0 15 5 L13 7 L11 5 L5 5 L3 7 Z M4 7 H12 L14 13 H2 Z" fill="var(--white)"/></svg>
      <span>555-014-2290</span>
    </div>
    <div class="contact__item">
      <svg class="contact__icon" viewBox="0 0 16 14"><rect x="1" y="2" width="14" height="10" fill="none" stroke="var(--white)" stroke-width="1.5"/><path d="M1 2 L8 8 L15 2" fill="none" stroke="var(--white)" stroke-width="1.5"/></svg>
      <span>briskcoatingstn@mailbox.com</span>
    </div>
  </div>
  <div class="front-url">
    <span class="front-url__rule"></span>
    <span>www.briskcoatingstn.com</span>
    <span class="front-url__rule"></span>
  </div>
</section>

</body>
</html>
```